International business needs business cards

Our company, DRV Ventures Inc. is in the business of supplying a range construction products with particular emphasis on CEMENT. We have developed our own brand - TORVAN SUPPLIES - with which to infiltrate the market. We are launching our brand of cement (TORVAN Type IS Cement) into the Caribbean which is unlike anything this market has ever seen. A monopoly has existed here for the past 60-odd years and the market has now opened to allow the importation of other brands and consumers are anxious and ready for change/improvement. We are very excited to be launching and want to make a great first impression. We will be conducting workshops and seminars (from government level to the hardware store owners) and we want our business card to give us the strong, confident introduction that we need.

Target Market(s)

construction; builders; engineers; home owners

Industry/Entity Type

Construction

Contact Information for Business Card

Marisol Depree
CEO
cell # 1 555 4180736
Ground floor,Lindell Plaza Suite 2734
George Town,Grand Cayman
Cayman Islands,KY1-4823
EMAIL: m.depree@drvventuresinc.example
web site drvventuresinc.example

COMPANY: skype info drv.ventures.example

second card
Yvette Brannock-Depree
CFO
CELL# 1 555 607 3941
George Town,Grand Cayman
Cayman Islands,KY1-4823
EMAIL: y.brannockdepree@drvventuresinc.example
website drvventuresinc.example

Requirements
Must have
• Business cards must display BOTH logos - DRV is the company and TORVAN is the brand.

```html
<!DOCTYPE html>
<html lang="en">
<head>
<meta charset="utf-8">
<title>DRV Ventures Inc. – Business Card</title>
<link rel="stylesheet" href="https://fonts.googleapis.com/css2?family=Open+Sans:wght@400;600;700&display=swap">
<style>
  :root {
    --maroon: #7b1518;
    --maroon-dark: #6a1114;
    --ink: #1a1a1a;
    --card-white: #f7f7f7;
    --stage: #e9e6e3;
    --white: #ffffff;
  }
  html, body {
    margin: 0;
    padding: 0;
    width: 1200px;
    height: 900px;
    overflow: hidden;
    background: var(--stage);
    font-family: "Open Sans", Arial, sans-serif;
  }
  .canvas {
    position: relative;
    width: 1200px;
    height: 900px;
  }
  .card {
    position: absolute;
    width: 604px;
    height: 372px;
    border-radius: 18px;
    overflow: hidden;
    box-shadow: 0 6px 22px rgba(0,0,0,0.18);
  }
  /* Front */
  .card-front {
    left: 120px;
    top: 44px;
    background: var(--card-white);
  }
  .holder-name {
    position: absolute;
    top: 20px;
    left: 0;
    width: 100%;
    text-align: center;
    margin: 0;
    font-size: 22px;
    font-weight: 600;
    color: var(--maroon);
  }
  .holder-title {
    position: absolute;
    top: 50px;
    left: 0;
    width: 100%;
    text-align: center;
    margin: 0;
    font-size: 15px;
    color: var(--ink);
  }
  .company-mark {
    position: absolute;
    top: 106px;
    left: 0;
    width: 100%;
    display: flex;
    justify-content: center;
    align-items: center;
    gap: 14px;
  }
  .company-mark .mark-square {
    width: 60px;
    height: 60px;
    background: var(--maroon);
  }
  .company-mark .mark-name {
    font-size: 34px;
    font-weight: 700;
    color: var(--ink);
    letter-spacing: 0.5px;
  }
  .contact-list {
    position: absolute;
    top: 218px;
    left: 0;
    width: 100%;
    margin: 0;
    padding: 0;
    list-style: none;
    text-align: center;
    font-size: 15px;
    color: var(--ink);
    line-height: 26px;
  }
  .contact-list svg {
    width: 11px;
    height: 11px;
    margin-right: 5px;
    vertical-align: -1px;
    fill: var(--maroon);
  }
  .address-band {
    position: absolute;
    left: 0;
    bottom: 0;
    width: 100%;
    height: 70px;
    background: var(--maroon);
    color: var(--white);
    text-align: center;
    font-size: 15.5px;
    line-height: 25px;
    padding-top: 10px;
    box-sizing: border-box;
  }
  /* Back */
  .card-back {
    left: 527px;
    top: 491px;
    background: var(--maroon);
  }
  .back-company {
    position: absolute;
    top: 150px;
    left: 0;
    width: 100%;
    text-align: center;
    font-size: 44px;
    font-weight: 700;
    color: var(--white);
    letter-spacing: 1px;
  }
  .brand-mark {
    position: absolute;
    right: 34px;
    bottom: 30px;
    display: flex;
    align-items: center;
    gap: 8px;
  }
  .brand-mark .brand-dot {
    width: 22px;
    height: 22px;
    border-radius: 50%;
    background: #c9c9c9;
  }
  .brand-mark .brand-name {
    font-size: 16px;
    font-weight: 600;
    color: #c9c9c9;
    letter-spacing: 1px;
  }
</style>
</head>
<body>
<main class="canvas">

  <section class="card card-front" aria-label="Business card front">
    <h1 class="holder-name">Marisol Depree</h1>
    <p class="holder-title">CEO</p>

    <div class="company-mark">
      <span class="mark-square"></span>
      <span class="mark-name">DRV Ventures Inc.</span>
    </div>

    <ul class="contact-list">
      <li>
        <svg viewBox="0 0 24 24" aria-hidden="true"><path d="M6.6 10.8a15.1 15.1 0 0 0 6.6 6.6l2.2-2.2c.3-.3.7-.4 1-.2 1.1.4 2.3.6 3.6.6.6 0 1 .4 1 1V20c0 .6-.4 1-1 1A17 17 0 0 1 3 4c0-.6.4-1 1-1h3.5c.6 0 1 .4 1 1 0 1.3.2 2.5.6 3.6.1.3 0 .7-.2 1z"/></svg>1 555 4180736
      </li>
      <li>
        <svg viewBox="0 0 24 24" aria-hidden="true"><path d="M2 5h20v14H2z M2 5l10 8 10-8" /></svg>m.depree@drvventuresinc.example
      </li>
      <li>
        <svg viewBox="0 0 24 24" aria-hidden="true"><circle cx="12" cy="12" r="11"/></svg>www.drvventuresinc.example
      </li>
    </ul>

    <div class="address-band">
      Ground floor, Lindell Plaza Suite 2734 George Town, Grand Cayman<br>
      Cayman Islands, KY1-4823
    </div>
  </section>

  <section class="card card-back" aria-label="Business card back">
    <div class="back-company">DRV Ventures Inc.</div>
    <div class="brand-mark">
      <span class="brand-dot"></span>
      <span class="brand-name">TORVAN</span>
    </div>
  </section>

</main>
</body>
</html>
```